Business Card Design

Looking for business card designs for a new business. there will be two cards of the same design (both lots of information below in contact info). We would like the logo diagonally across the card with the information split above and below the logo similar to sketch. happy to look at similar alternatives
Please use same colours as in logo design

Industry/Entity Type

Business

Contact Information for Business Card

Dwight Halloran
mob - 0491 738 204
ph - 02 6148 3920
fax - 02 6148 3975
email - dwight@kestrelbeams.com.au
14 Larkmoor Road, Taminda NSW 2340

Colin Marchetti
mob - 0438 912 557
ph - 02 6148 3920
fax - 02 6148 3975
email - colin@kestrelbeams.com.au

```html
<!DOCTYPE html>
<html lang="en">
<head>
<meta charset="utf-8">
<title>Kestrel Beams &amp; Trusses – Business Card</title>
<link rel="stylesheet" href="https://fonts.googleapis.com/css2?family=Open+Sans:wght@400;600;700;800&display=swap">
<style>
  :root {
    --teal: #0d7b78;
    --ink: #111111;
    --paper: #ffffff;
    --backdrop: #e6e6e4;
    --text: #222222;
  }
  * { box-sizing: border-box; margin: 0; padding: 0; }
  html, body {
    width: 1112px;
    height: 1200px;
    overflow: hidden;
    background: var(--backdrop);
    font-family: "Open Sans", Arial, sans-serif;
  }
  .card {
    position: absolute;
    width: 951px;
    height: 545px;
    overflow: hidden;
  }
  .card--front { left: 25px; top: 44px; background: var(--paper); }
  .card--back { left: 140px; top: 616px; background: var(--ink); }

  .brand {
    position: absolute;
    display: flex;
    align-items: center;
    gap: 22px;
  }
  .brand__mark { width: 64px; height: 64px; flex: none; background: var(--teal); }
  .brand__name {
    font-weight: 800;
    line-height: 0.98;
    letter-spacing: -1px;
  }
  .card--front .brand { left: 194px; top: 70px; }
  .card--front .brand__name { color: var(--ink); font-size: 56px; }

  .card--back .brand { left: 126px; top: 178px; }
  .card--back .brand__name { color: var(--teal); font-size: 66px; }

  .contact {
    position: absolute;
    top: 262px;
    font-size: 22px;
    color: var(--text);
    line-height: 37px;
  }
  .contact--office { right: 542px; text-align: right; }
  .contact--direct { left: 442px; }
  .contact__divider {
    position: absolute;
    left: 426px;
    top: 268px;
    width: 1.5px;
    height: 104px;
    background: var(--text);
  }
  .contact__line { display: flex; align-items: center; gap: 6px; white-space: nowrap; }
  .contact--office .contact__line { justify-content: flex-end; }
  .contact__line--email { font-size: 19px; }
  .icon { width: 18px; height: 18px; flex: none; }

  .swoosh { position: absolute; left: 0; top: 0; width: 951px; height: 545px; }

  .holder {
    position: absolute;
    right: 74px;
    top: 476px;
    color: var(--paper);
    font-size: 26px;
    font-weight: 700;
  }

  .web {
    position: absolute;
    left: 0;
    right: 0;
    top: 425px;
    text-align: center;
    color: var(--paper);
    font-size: 30px;
    letter-spacing: 2.5px;
  }
  .web__domain { font-weight: 600; }
</style>
</head>
<body>

<section class="card card--front" aria-label="Business card front">
  <svg class="swoosh" viewBox="0 0 951 545" aria-hidden="true">
    <path d="M0,470 C200,505 420,520 600,495 C760,472 870,455 951,462 L951,545 L0,545 Z" fill="var(--teal)"/>
    <path d="M0,462 C200,496 420,512 600,487 C760,464 870,447 951,454 L951,458 C870,452 760,468 600,491 C420,516 200,500 0,466 Z" fill="var(--paper)"/>
    <path d="M0,414 C180,462 360,500 520,495 C690,490 830,440 951,458 L951,468 C830,452 690,500 520,506 C340,512 160,478 0,440 Z" fill="var(--ink)"/>
  </svg>

  <div class="brand">
    <span class="brand__mark"></span>
    <span class="brand__name">Kestrel<br>Beams &amp; Trusses</span>
  </div>

  <div class="contact contact--office">
    <div class="contact__line">
      <svg class="icon" viewBox="0 0 20 20" aria-hidden="true"><circle cx="10" cy="10" r="8.5" fill="none" stroke="currentColor" stroke-width="1.5"/><path d="M7 5.5 L8.6 8 L7.6 9 C8.3 10.6 9.4 11.7 11 12.4 L12 11.4 L14.5 13 L13.4 14.6 C9.6 14.2 5.8 10.4 5.4 6.6 Z" fill="currentColor"/></svg>
      <span>02 6148 3920</span>
    </div>
    <div class="contact__line">14 Larkmoor Road</div>
    <div class="contact__line">Corvalla NSW 2361</div>
  </div>

  <div class="contact__divider"></div>

  <div class="contact contact--direct">
    <div class="contact__line">
      <svg class="icon" viewBox="0 0 20 20" aria-hidden="true"><rect x="5" y="1.5" width="10" height="17" rx="1.5" fill="none" stroke="currentColor" stroke-width="1.6"/><rect x="7" y="4" width="6" height="6" fill="currentColor"/><rect x="7" y="12" width="6" height="4" fill="currentColor"/></svg>
      <span>0438 912 557</span>
    </div>
    <div class="contact__line">
      <svg class="icon" viewBox="0 0 20 20" aria-hidden="true"><rect x="6" y="2" width="8" height="6" fill="none" stroke="currentColor" stroke-width="1.5"/><path d="M2 8 H18 V16 H2 Z" fill="currentColor"/><rect x="5" y="14" width="10" height="4" fill="currentColor"/></svg>
      <span>02 6148 3975</span>
    </div>
    <div class="contact__line contact__line--email">
      <svg class="icon" viewBox="0 0 20 20" aria-hidden="true"><path d="M2 8 L10 3 L18 8 V17 H2 Z" fill="none" stroke="currentColor" stroke-width="1.6"/><path d="M2 8 L10 13 L18 8" fill="none" stroke="currentColor" stroke-width="1.6"/></svg>
      <span>colin@kestrelbeams.com.au</span>
    </div>
  </div>

  <div class="holder">Colin Marchetti</div>
</section>

<section class="card card--back" aria-label="Business card back">
  <div class="brand">
    <span class="brand__mark"></span>
    <span class="brand__name">Kestrel<br>Beams &amp; Trusses</span>
  </div>
  <div class="web">www.<span class="web__domain">kestrelbeams</span>.com.au</div>
</section>

</body>
</html>
```